Cozy Cradle Loops Needs a Beautiful Website

I need a new website for this new E-commerce. I sell handmade baby crochets, e.g. booties, headbands, hats, etc. I need a feminine and soft design to make the moms-to-be say 'oohh ahh'. I'd like pink, blue and gray. I'd like an inviting homepage, and nice regular pages where people can see and order the products.

Industry/Entity Type

Baby

Requirements
Must have
• beautiful, soft, feminine design. Please use pictures of the colors I'd like: brown, yellow, pink and blue. Any combination, but definitely include brown.

```html
<!DOCTYPE html>
<html lang="en">
<head>
<meta charset="utf-8">
<title>Cozy Cradle Loops</title>
<link href="https://fonts.googleapis.com/css2?family=Grand+Hotel&family=Nunito:wght@400;600;700&display=swap" rel="stylesheet">
<style>
:root{
  --pink:#e966ad;
  --pink-deep:#e0559f;
  --pink-soft:#fbe1ee;
  --pink-bg:#f8c9e2;
  --pink-glow:#ef86bf;
  --blue:#35b8d8;
  --blue-dark:#1f9fc0;
  --gray:#666;
  --gray-light:#999;
  --paper:#fbf8f9;
  --white:#fff;
}
*{margin:0;padding:0;box-sizing:border-box}
html,body{width:836px;height:1200px;overflow:hidden}
body{font-family:"Nunito",sans-serif;color:var(--gray);background:var(--pink-bg)}
.canvas{position:relative;width:836px;height:1200px;overflow:hidden;
  background:linear-gradient(90deg,#f4a9d0 0%,#fbd3e8 11%,#fde6f2 50%,#fbd3e8 89%,#fcdff0 100%)}
.page{position:absolute;left:91px;top:0;width:654px;height:994px;background:var(--paper)}
.abs{position:absolute}
.script{font-family:"Grand Hotel",cursive;font-weight:400}

/* top bar */
.topbar{top:14px;left:16px;right:18px;height:16px;font-size:9px;color:#444}
.cart-link{position:absolute;left:0;top:0;display:flex;align-items:center;gap:7px}
.cart-link em{font-style:normal;color:var(--pink)}
.account-links{position:absolute;right:0;top:0;display:flex;gap:20px}
.account-links .active{color:var(--blue)}

/* nav */
.nav{top:42px;left:0;width:654px;height:44px;background:var(--pink)}
.nav a{position:absolute;top:0;height:44px;line-height:44px;color:var(--white);font-size:18px;text-decoration:none}
.nav .current{background:var(--pink-deep);padding:0 21px;left:0}
.logo{left:327px;top:16px;width:92px;height:92px;margin-left:-46px;border-radius:50%;background:var(--white);
  border:3px solid var(--pink-soft);display:flex;align-items:center;justify-content:center;text-align:center}
.logo span{font-weight:700;color:var(--pink);font-size:12px;line-height:1.1;width:70px}

/* hero */
.hero-frame{left:9px;top:93px;width:637px;height:258px;border:1px solid #f3dbe6;background:var(--white)}
.hero-photo{left:18px;top:101px;width:405px;height:238px;background:radial-gradient(ellipse at 45% 55%,#e8a7bf 0%,#d99ab3 30%,#cfc9c9 60%,#bdb7b6 100%)}
.hero-panel{left:419px;top:101px;width:217px;height:238px;background:var(--pink-soft);border-radius:12px 0 0 12px}
.hero-title{left:432px;top:138px;width:190px;text-align:center;font-size:23px;line-height:27px;color:var(--pink)}
.hero-title .b{color:var(--blue)}
.hero-sub{left:432px;top:228px;width:190px;text-align:center;font-size:19px;color:var(--pink)}
.btn-hero{left:446px;top:269px;width:170px;height:25px;background:var(--blue);color:var(--white);font-size:9px;font-weight:600;text-align:center;line-height:25px;border-radius:3px;box-shadow:0 2px 0 var(--blue-dark)}
.hero-arrows{left:514px;top:310px}

/* products */
.h2{font-size:22px;color:var(--pink)}
.products-title{left:18px;top:361px}
.products-intro{left:18px;top:392px;font-size:8.5px;color:var(--gray)}
.card{width:128px;height:115px;background:var(--white);border:1px solid #eee;box-shadow:0 1px 3px rgba(0,0,0,.08)}
.card .photo{position:absolute;left:8px;top:8px;width:112px;height:101px}
.item-name{font-size:9px;color:var(--gray)}
.price{font-size:11px;color:var(--pink);font-style:italic;font-weight:600}
.btn-cart{width:85px;height:19px;background:var(--blue);color:var(--white);font-size:9px;font-weight:600;text-align:center;line-height:19px;border-radius:3px;box-shadow:0 2px 0 var(--blue-dark)}

/* sidebar */
.promo{left:455px;width:180px;height:89px}
.promo-1{top:370px;background:linear-gradient(90deg,#e3d5cf 0%,#f3ece8 60%,#eae3df 100%)}
.promo-2{top:475px;background:linear-gradient(90deg,#5b6470 0%,#7a7d84 60%,#9b9a9c 100%)}
.promo-1 .t1{position:absolute;right:24px;top:10px;font-size:13px;font-weight:700;color:var(--pink)}
.promo-1 .t2{position:absolute;right:8px;top:24px;font-size:17px;color:#555}
.promo-1 .t3{position:absolute;right:8px;top:42px;font-size:14px;color:var(--white)}
.btn-pink{position:absolute;height:17px;background:var(--pink);color:var(--white);font-size:8px;font-weight:700;line-height:17px;text-align:center}
.promo-2 .t1{position:absolute;left:8px;top:11px;font-size:10px;font-weight:700;color:var(--white)}
.promo-2 .t2{position:absolute;left:8px;top:24px;font-size:24px;font-weight:700;font-style:italic;color:var(--blue)}
.promo-2 .t3{position:absolute;left:58px;top:36px;font-size:11px;color:var(--white);font-style:italic}
.tweets-title{left:455px;top:590px;width:180px;border-bottom:1px solid #ddd;font-size:17px;color:var(--pink);height:24px}
.tweet{left:456px;width:182px;font-size:8.5px;line-height:14px;color:#555}
.tweet .hl{color:var(--blue)}
.tweet small{display:block;font-size:7.5px;color:var(--gray-light);margin-top:1px}

.divider{left:18px;top:796px;width:618px;border-top:1px dashed var(--pink)}
.welcome-title{left:18px;top:813px}
.welcome p{font-size:8.4px;line-height:15.7px;color:#555;margin-bottom:15px}
.welcome{left:18px;top:852px;width:410px}
.blog-title{left:455px;top:813px}
.blog-photo{left:455px;top:849px;width:181px;height:116px;background:linear-gradient(135deg,#3c3c44 0%,#e9e2d0 30%,#f2d35c 45%,#5b8ea6 60%,#8a6a52 75%,#c2404a 100%)}

/* footer */
.footer{left:0;top:994px;width:836px;height:206px;background:var(--pink)}
.f-col{top:1040px;color:var(--white)}
.f-col h3{font-size:16px;margin-bottom:8px}
.f-col li{list-style:none;font-size:9.2px;line-height:17.6px}
.f-call{left:443px;top:1063px;color:var(--white);font-size:8.5px;line-height:12px}
.f-call b{display:block;font-family:"Grand Hotel",cursive;font-weight:400;font-size:15px;line-height:14px}
.follow-art{left:516px;top:1036px;width:90px;height:74px;border-radius:8px;background:radial-gradient(ellipse at 50% 50%,var(--pink-glow) 0%,var(--pink) 75%)}
.social{top:1042px;width:24px;height:24px;border:1.5px solid var(--white);border-radius:50%;color:var(--white);font-size:6.5px;font-weight:700;line-height:21px;text-align:center}
.email{left:601px;top:1100px;width:144px;height:30px;border:1px solid var(--white);color:var(--white);font-size:9px;line-height:28px;padding-left:9px}
.email .go{position:absolute;right:0;top:0;width:31px;height:28px;border-left:1px solid var(--white)}
.f-rule{left:91px;top:1162px;width:654px;border-top:1px dashed rgba(255,255,255,.6)}
.copy{left:0;top:1176px;width:836px;text-align:center;color:var(--white);font-size:8px}
</style>
</head>
<body>
<div class="canvas">
  <div class="page">
    <div class="abs topbar">
      <div class="cart-link">
        <svg width="14" height="12" viewBox="0 0 14 12"><path d="M0 1h2.5l2 7h7l1.8-5H4" fill="none" stroke="#e966ad" stroke-width="1.6"/><circle cx="5.5" cy="10.5" r="1.2" fill="#e966ad"/><circle cx="10.5" cy="10.5" r="1.2" fill="#e966ad"/></svg>
        <span>Cart <em>(0.00)</em> Items</span>
      </div>
      <div class="account-links"><span>My Account</span><span>Cart</span><span class="active">Login</span><span>Check out</span></div>
    </div>

    <nav class="abs nav script">
      <a class="current">Home</a>
      <a style="left:91px">About Us</a>
      <a style="left:174px">New Arrival</a>
      <a style="left:405px">Baby Crochets</a>
      <a style="left:513px">Blog</a>
      <a style="left:568px">Contact Us</a>
    </nav>
    <div class="abs logo"><span>Cozy Cradle Loops</span></div>

    <div class="abs hero-frame"></div>
    <div class="abs hero-photo" role="img" aria-label="Pink crocheted baby booties with rose details on white lace"></div>
    <div class="abs hero-panel"></div>
    <div class="abs hero-title script">Delicious <span class="b">Handmade</span><br><span class="b">Baby Crochets</span> for<br>Your Babies</div>
    <div class="abs hero-sub script">Booties, Headbands, Hats</div>
    <div class="abs btn-hero">FIND OUT MORE ABOUT US</div>
    <svg class="abs hero-arrows" width="38" height="16" viewBox="0 0 38 16">
      <circle cx="8" cy="8" r="7" fill="none" stroke="#e966ad" stroke-width="1.3"/><path d="M9.5 5 6.5 8l3 3" fill="none" stroke="#e966ad" stroke-width="1.3"/>
      <circle cx="27" cy="8" r="7" fill="none" stroke="#e966ad" stroke-width="1.3"/><path d="M25.5 5l3 3-3 3" fill="none" stroke="#e966ad" stroke-width="1.3"/>
    </svg>

    <h2 class="abs h2 script products-title">Our Products</h2>
    <p class="abs products-intro">Check our all latest products int his section</p>

    <div class="abs card" style="left:18px;top:421px"><div class="photo" role="img" aria-label="Pink crocheted crown headband" style="background:linear-gradient(135deg,#f6a9cb,#f07bb0)"></div></div>
    <div class="abs card" style="left:158px;top:421px"><div class="photo" role="img" aria-label="Cream crocheted booties with red flowers" style="background:linear-gradient(135deg,#5b5148,#e8dfcf 55%,#b6434f)"></div></div>
    <div class="abs card" style="left:299px;top:421px"><div class="photo" role="img" aria-label="Black crocheted baby sneakers" style="background:linear-gradient(135deg,#3a3a3e,#6b6b70 60%,#d9d9d9)"></div></div>
    <span class="abs item-name" style="left:21px;top:548px">Booties for baby</span><span class="abs price" style="left:107px;top:547px">$56.00</span>
    <span class="abs item-name" style="left:160px;top:548px">Booties for baby</span><span class="abs price" style="left:247px;top:547px">$56.00</span>
    <span class="abs item-name" style="left:301px;top:548px">Booties for baby</span><span class="abs price" style="left:388px;top:547px">$56.00</span>
    <div class="abs btn-cart" style="left:41px;top:567px">Add to Cart</div>
    <div class="abs btn-cart" style="left:181px;top:567px">Add to Cart</div>
    <div class="abs btn-cart" style="left:322px;top:567px">Add to Cart</div>

    <div class="abs card" style="left:18px;top:603px"><div class="photo" role="img" aria-label="Mint crocheted booties on tree bark" style="background:linear-gradient(135deg,#4b3e33,#8fd3d1 55%,#5d4a3c)"></div></div>
    <div class="abs card" style="left:158px;top:603px"><div class="photo" role="img" aria-label="Bright pink crocheted crown" style="background:linear-gradient(135deg,#f4f0f2,#ea6fc0 55%,#f4eef1)"></div></div>
    <div class="abs card" style="left:299px;top:603px"><div class="photo" role="img" aria-label="Red crocheted booties with cream flower" style="background:linear-gradient(135deg,#c9424c,#e26b6b 55%,#e8d6ad)"></div></div>
    <span class="abs item-name" style="left:21px;top:730px">Booties for baby</span><span class="abs price" style="left:107px;top:729px">$56.00</span>
    <span class="abs item-name" style="left:160px;top:730px">Booties for baby</span><span class="abs price" style="left:247px;top:729px">$56.00</span>
    <span class="abs item-name" style="left:301px;top:730px">Booties for baby</span><span class="abs price" style="left:388px;top:729px">$56.00</span>
    <div class="abs btn-cart" style="left:41px;top:749px">Add to Cart</div>
    <div class="abs btn-cart" style="left:181px;top:749px">Add to Cart</div>
    <div class="abs btn-cart" style="left:322px;top:749px">Add to Cart</div>

    <div class="abs promo promo-1" role="img" aria-label="Sleeping baby in a blue crocheted hat">
      <span class="t1">Exclusive</span><span class="t2 script">Discount</span><span class="t3 script">Baby Crochets</span>
      <span class="btn-pink" style="right:0;top:64px;width:74px">KNOW MORE</span>
    </div>
    <div class="abs promo promo-2" role="img" aria-label="Navy crocheted sneakers with red stars">
      <span class="t1">Get Special</span><span class="t2">50%</span><span class="t3">OFF</span>
      <span class="btn-pink" style="left:0;top:64px;width:74px">KNOW MORE</span>
    </div>

    <div class="abs tweets-title script">Tweeter News</div>
    <svg class="abs" style="left:621px;top:592px" width="14" height="14"><circle cx="7" cy="7" r="6" fill="#35b8d8"/></svg>
    <div class="abs tweet" style="top:628px"><span class="hl">@ Neque porro</span> quisquam est quid<small>Lorem ipsum dolor sit amet, consectetur adipisicin</small></div>
    <div class="abs tweet" style="top:673px">@ Neque porro quisq<span class="hl">uam est quidAt ve</span>ro eos<br>&nbsp;et accusamus et iusto odio dign<small>Lorem ipsum dolor sit amet, consectetur adipisicin</small></div>
    <div class="abs tweet" style="top:734px"><span class="hl">@ Neque porro</span> quisquam est quid<small>Lorem ipsum dolor sit amet, consectetur adipisicin</small></div>

    <div class="abs divider"></div>
    <h2 class="abs h2 script welcome-title">Welcome to Our Site!!</h2>
    <div class="abs welcome">
      <p>At vero eos et accusamus et iusto odio dignissimos ducimus qui blanditiis praesentium voluptatum deleniti atque corrupti quos dolores et quas molestias excepturi sint occaecati cupiditate non provident, similique sunt in culpa qui officia deserunt mollitia animi, id est laborum et dolorum fuga. Et harum quidem rerum facilis est et expedita distinctio.</p>
      <p>Nam libero tempore, cum soluta nobis est eligendi optio cumque nihil impedit quo minus id quod maxime placeat facere possimus, omnis voluptas assumenda est, omnis dolor repellendus. Temporibus a</p>
    </div>
    <h2 class="abs h2 script blog-title">Our Blog</h2>
    <div class="abs blog-photo" role="img" aria-label="Grid of six pairs of colourful crocheted baby sneakers"></div>
  </div>

  <footer class="abs footer"></footer>
  <div class="abs f-col" style="left:90px"><h3 class="script">Products</h3><ul><li>Booties,</li><li>Headbands,</li><li>Hats</li><li>Etc</li></ul></div>
  <div class="abs f-col" style="left:185px"><h3 class="script">Site Info</h3><ul><li>About</li><li>Menu</li><li>Portions &amp; Prices</li><li>Payment &amp; Delivery</li></ul></div>
  <div class="abs f-col" style="left:309px"><h3 class="script">Conatct Details</h3><ul><li>lorem ipsum lorem sit</li><li>12 Willow Lane</li><li>Millbrook Town</li><li>Eastshire EA4 2QP</li></ul></div>
  <div class="abs f-call"><b>Call</b>07000 123 456<br><br><b>Mial</b>hello@cozycradleloops.example</div>
  <div class="abs follow-art" role="img" aria-label="Hand-lettered 'Follow Us' with a curved arrow"></div>
  <div class="abs social" style="left:617px">LIKE</div>
  <div class="abs social" style="left:646px">CHAT</div>
  <div class="abs social" style="left:677px">FEED</div>
  <div class="abs social" style="left:706px">PLUS</div>
  <div class="abs email">Email:
    <div class="go"><svg width="31" height="28" viewBox="0 0 31 28"><rect x="6" y="8" width="19" height="13" fill="#fff"/><path d="M6 8l9.5 7L25 8" fill="none" stroke="#e966ad" stroke-width="1.4"/></svg></div>
  </div>
  <div class="abs f-rule"></div>
  <div class="abs copy">© Copyright 2014 all rights are reseved</div>
</div>
</body>
</html>
```